Business Card Design

I already have a company logo for my company. I have a logo for the manufacturer we represent. I want a professional business card design.

```html
<!DOCTYPE html>
<html lang="en">
<head>
<meta charset="utf-8">
<title>Signalpost Solutions – Business Card</title>
<link href="https://fonts.googleapis.com/css2?family=Open+Sans:wght@400;600;700;800&display=swap" rel="stylesheet">
<style>
  :root {
    --stage: #2a2a2c;
    --card: #1f1f22;
    --card-edge: #18181a;
    --text: #f2f2f2;
    --red: #e41e26;
    --gold: #d8a024;
    --rule: #8a8a8e;
    --pattern-dark: #1b1b1d;
    --pattern-light: #34343a;
  }
  * { box-sizing: border-box; margin: 0; padding: 0; }
  html, body { width: 1200px; height: 780px; overflow: hidden; }
  body {
    background: var(--stage);
    font-family: "Open Sans", Arial, sans-serif;
    color: var(--text);
    position: relative;
  }
  .card {
    position: absolute;
    top: 235px;
    width: 540px;
    height: 310px;
    border-radius: 22px;
    background: var(--card);
    box-shadow: 0 3px 0 var(--card-edge), 0 6px 0 #141416, 0 22px 40px rgba(0,0,0,.45);
    overflow: hidden;
  }
  .card--front { left: 40px; }
  .card--back { left: 620px; }

  .brand {
    position: absolute;
    left: 44px;
    top: 58px;
    display: flex;
    align-items: center;
    gap: 12px;
  }
  .brand__square { width: 26px; height: 26px; background: var(--red); flex: none; }
  .brand__name {
    font-weight: 800;
    font-size: 18px;
    line-height: 1.15;
    color: var(--text);
    text-transform: uppercase;
    letter-spacing: .5px;
  }

  .divider {
    position: absolute;
    left: 0; top: 0;
  }

  .person {
    position: absolute;
    left: 272px;
    right: 44px;
    top: 70px;
  }
  .person__name {
    font-weight: 800;
    font-size: 28px;
    line-height: 1.1;
    white-space: nowrap;
  }
  .person__first { color: var(--red); }
  .person__last { color: var(--gold); }
  .person__title {
    font-weight: 600;
    font-size: 15px;
    margin-top: 2px;
  }

  .contacts {
    list-style: none;
    position: absolute;
    left: 272px;
    top: 158px;
    font-size: 15px;
    line-height: 22px;
  }
  .contacts li { display: flex; align-items: center; gap: 9px; }
  .contacts svg { width: 13px; height: 13px; flex: none; }

  .address {
    position: absolute;
    left: 44px;
    bottom: 34px;
    font-size: 14px;
  }

  .back__pattern {
    position: absolute;
    inset: 0;
    background: linear-gradient(120deg, var(--pattern-dark) 0%, #222226 55%, var(--pattern-light) 100%);
  }
  .back__brand {
    position: absolute;
    right: 30px;
    bottom: 26px;
    display: flex;
    align-items: center;
    gap: 6px;
  }
  .back__brand .brand__square { width: 10px; height: 10px; }
  .back__brand .brand__name { font-size: 9px; font-weight: 800; }
</style>
</head>
<body>

  <section class="card card--front" aria-label="Business card front">
    <div class="brand">
      <span class="brand__square"></span>
      <span class="brand__name">Signalpost<br>Solutions LLC</span>
    </div>

    <svg class="divider" width="540" height="310" aria-hidden="true">
      <line x1="262" y1="40" x2="170" y2="190" stroke="var(--rule)" stroke-width="1"/>
    </svg>

    <div class="person">
      <p class="person__name"><span class="person__first">Halvard</span> <span class="person__last">Trenko</span></p>
      <p class="person__title">Managing Director</p>
    </div>

    <ul class="contacts">
      <li>
        <svg viewBox="0 0 16 16" aria-hidden="true"><path fill="var(--red)" d="M3.6 1.2l2.3 2.6-1.3 1.8c.9 2 2.4 3.6 4.4 4.6l1.8-1.3 2.7 2.3-1.1 2.4C7.3 13.4 2.6 8.8 1.2 2.5z"/></svg>
        (555) 014-2290
      </li>
      <li>
        <svg viewBox="0 0 16 16" aria-hidden="true"><rect x="1" y="3" width="14" height="10" rx="1.5" fill="var(--red)"/><path d="M2 4.5l6 4.5 6-4.5" stroke="var(--card)" stroke-width="1.3" fill="none"/></svg>
        hello@signalpostco.com
      </li>
      <li>
        <svg viewBox="0 0 16 16" aria-hidden="true"><circle cx="8" cy="8" r="6.5" fill="var(--red)"/><path d="M1.5 8h13M8 1.5c-3 3.5-3 9.5 0 13M8 1.5c3 3.5 3 9.5 0 13" stroke="var(--card)" stroke-width="1" fill="none"/></svg>
        www.signalpostco.com
      </li>
    </ul>

    <p class="address">1840 Ridgeline Ave. Suite 310 Dallas, TX 75201</p>
  </section>

  <section class="card card--back" aria-label="Business card back">
    <div class="back__pattern" role="img" aria-label="Tonal repeating brand pattern in dark grey"></div>
    <div class="back__brand">
      <span class="brand__square"></span>
      <span class="brand__name">Signalpost Solutions</span>
    </div>
  </section>

</body>
</html>
```